Business card design for a dynamic IT consulting company

We need a business card design for a young firm, specialized in the Telecommunications/Consulting industry. The name of the company is Quindor and Partners Business Consulting Ltd. (Short name: Quindor and Partnes)
Quindor = solve read reverse, so we aim to be uncomplicated and solution-oriented. The small pipe in our logo is also related to the word solve. So we need a new business card design, which is simple, eye catching and something non traditional (I would probably prefer a square shaped design rather than a rectangle, but open for suggestions). Attached our logo.

Target Market(s)

Usually our customers are Tier1 Telecoms providers (Q-Netra, Palorix, etc) and their executives.

Industry/Entity Type

Business

Contact Information for Business Card

Name: Bence Tolnavari
Email: b.tolnavari@quindor.hu
Web: www.quindor.hu
Mobile: +36 30 518 2769
Title: Managing Director

Optional:
Company name: Quindor and Partners Ltd.
Address: 1087 Budapest, Tolvenka str. 28/C, Hungary

Font styles to use
Other font styles liked:
• helveticaneue_medium, Prime Regular are used now.

Colors

Designer to choose colors to be used in the design.

Requirements
Must have
• I would like to have a 2 sided design.
Nice to have
• I thought if we make the logo a bit bigger (without the company name), that could go to the back with the company name below. I though, if the pipe in the logo is somehow touchable on the business card, would be nice and unique.

```html
<!DOCTYPE html>
<html lang="en">
<head>
<meta charset="utf-8">
<title>Quindor and Partners – Business Card</title>
<link rel="stylesheet" href="https://fonts.googleapis.com/css2?family=Exo+2:wght@500;600&family=Arimo:wght@400;500&display=swap">
<style>
  :root {
    --backdrop: #3b3430;
    --card: #1c1c1d;
    --card-edge: #111112;
    --ink-white: #f2f2f2;
    --ink-grey: #5f5f61;
    --magenta: #b8379c;
    --cyan: #2ba3dc;
  }
  * { margin: 0; padding: 0; box-sizing: border-box; }
  html, body { width: 1200px; height: 780px; overflow: hidden; }
  body {
    background: var(--backdrop);
    font-family: "Arimo", Arial, sans-serif;
    position: relative;
  }
  .card {
    position: absolute;
    top: 235px;
    width: 540px;
    height: 310px;
    border-radius: 20px;
    background: var(--card);
    border: 1px solid var(--card-edge);
  }
  .card--front { left: 40px; }
  .card--back { left: 620px; }

  /* Front: company name */
  .brand {
    position: absolute;
    left: 0; right: 0; top: 0; bottom: 0;
    display: flex; align-items: center; justify-content: center;
    gap: 14px;
  }
  .brand__square { width: 16px; height: 16px; background: var(--ink-grey); }
  .brand__name {
    font-family: "Exo 2", sans-serif;
    font-weight: 500;
    font-size: 34px;
    color: var(--ink-grey);
    letter-spacing: 0.5px;
  }

  /* Back: contact side */
  .mark {
    position: absolute;
    left: 40px; top: 108px;
    width: 150px;
    display: flex; align-items: center; gap: 10px;
  }
  .mark__square { width: 14px; height: 14px; background: var(--magenta); flex: none; }
  .mark__name {
    font-family: "Exo 2", sans-serif;
    font-weight: 600;
    font-size: 26px;
    color: var(--ink-white);
  }
  .divider {
    position: absolute;
    left: 205px; top: 80px;
    width: 1.5px; height: 115px;
    background: var(--magenta);
  }
  .contact {
    position: absolute;
    left: 225px; top: 86px;
  }
  .contact__name {
    font-family: "Exo 2", sans-serif;
    font-weight: 600;
    font-size: 23px;
    color: var(--ink-white);
    letter-spacing: 0.5px;
  }
  .contact__title {
    font-size: 15px;
    color: var(--magenta);
    margin-bottom: 8px;
  }
  .contact__list { list-style: none; }
  .contact__item {
    display: flex; align-items: center; gap: 9px;
    font-size: 15px;
    line-height: 22px;
    color: var(--ink-white);
  }
  .contact__icon { width: 13px; height: 13px; flex: none; }
  .address {
    position: absolute;
    left: 60px; top: 238px;
    font-size: 16px;
    color: var(--ink-white);
  }
</style>
</head>
<body>
  <section class="card card--front" aria-label="Card front">
    <div class="brand">
      <span class="brand__square"></span>
      <span class="brand__name">Quindor</span>
    </div>
  </section>

  <section class="card card--back" aria-label="Card back">
    <div class="mark">
      <span class="mark__square"></span>
      <span class="mark__name">Quindor</span>
    </div>
    <div class="divider"></div>
    <div class="contact">
      <div class="contact__name">Bence Tolnavari</div>
      <div class="contact__title">Managing Director</div>
      <ul class="contact__list">
        <li class="contact__item">
          <svg class="contact__icon" viewBox="0 0 13 13" aria-hidden="true"><rect x="3" y="0.8" width="7" height="11.4" rx="1" fill="none" stroke="#b8379c" stroke-width="1.4"/></svg>
          +36 30 518 2769
        </li>
        <li class="contact__item">
          <svg class="contact__icon" viewBox="0 0 13 13" aria-hidden="true"><rect x="0.5" y="2.5" width="12" height="8" fill="#f2f2f2"/><path d="M0.5 2.5 L6.5 7 L12.5 2.5" fill="none" stroke="#1c1c1d" stroke-width="1"/></svg>
          b.tolnavari@quindor.hu
        </li>
        <li class="contact__item">
          <svg class="contact__icon" viewBox="0 0 13 13" aria-hidden="true"><circle cx="6.5" cy="6.5" r="6" fill="#2ba3dc"/><path d="M0.5 6.5 H12.5 M6.5 0.5 C3.5 4 3.5 9 6.5 12.5 M6.5 0.5 C9.5 4 9.5 9 6.5 12.5" fill="none" stroke="#1c1c1d" stroke-width="0.8"/></svg>
          www.quindor.hu
        </li>
      </ul>
    </div>
    <div class="address">1087 Budapest, Tolvenka str. 28/C, Hungary</div>
  </section>
</body>
</html>
```